Company raising consciousness thru leadership & self-awareness needs amazing Letterhead

We are a technology company that spun out of a consulting firm. We are waking people up in corporate America through surveys, leadership development, workshops and consulting. Getting employees to become self-aware and changing company culture through improved leadership and team effectiveness. We need Word letterhead for our proposals, handouts, and worksheets that match our brand standard, is fresh, and communicates trust, credibility and professionalism.

Our target clients are other businesses, and executive leaders and C-suite leaders in those companies.

Sans Serif

• A Word template we can use for handouts, proposals, executive summary, project management documents, and letters. We need our logo. Please add page number and date on the footer. Must match the theme of our new website in look and feel to match the brand we are trying to promote. Use the colors from our brand standard document I submitted.

```html
<!DOCTYPE html>
<html lang="en">
<head>
<meta charset="utf-8">
<title>Veridan Letterhead</title>
<link href="https://fonts.googleapis.com/css2?family=Poppins:wght@400;500;600&display=swap" rel="stylesheet">
<style>
  :root {
    --navy: #1f2d5c;
    --purple: #7b3f98;
    --sky: #2aa7df;
    --ink: #5a5a62;
    --rule: #6e5b9a;
    --paper: #ffffff;
    --backdrop: #eeeef2;
  }
  * { margin: 0; padding: 0; box-sizing: border-box; }
  html, body { width: 1200px; height: 1200px; overflow: hidden; }
  body {
    background: var(--backdrop);
    font-family: "Poppins", sans-serif;
    color: var(--ink);
    position: relative;
  }
  .sheet {
    position: absolute;
    top: 250px;
    width: 540px;
    height: 700px;
    background: var(--paper);
    box-shadow: 0 6px 24px rgba(30, 30, 60, 0.12);
  }
  .sheet--front { left: 40px; }
  .sheet--inner { left: 620px; }

  .brand { position: absolute; display: flex; align-items: center; gap: 8px; }
  .brand__dot { width: 14px; height: 14px; border-radius: 50%; background: var(--sky); }
  .brand__name {
    font-family: "Poppins", sans-serif;
    font-weight: 600;
    font-size: 26px;
    letter-spacing: 2px;
    color: var(--navy);
  }
  .sheet--front .brand { left: 40px; top: 60px; }
  .sheet--inner .brand { left: 40px; top: 44px; }

  .rule { position: absolute; height: 1px; background: var(--rule); }
  .bar { position: absolute; height: 4px; background: var(--purple); }

  .recipient { position: absolute; left: 40px; top: 150px; width: 120px; font-size: 8px; line-height: 1.5; }
  .recipient__label { color: var(--ink); }
  .recipient__name { color: var(--navy); font-weight: 500; font-size: 10px; }
  .recipient__date-label { margin-top: 18px; color: var(--navy); font-weight: 500; font-size: 10px; }

  .letter { position: absolute; left: 175px; top: 140px; width: 330px; }
  .letter__greeting { color: var(--navy); font-weight: 500; font-size: 12px; margin-bottom: 12px; }
  .letter p { font-size: 8.5px; line-height: 1.6; margin-bottom: 14px; }

  .signature { position: absolute; left: 175px; top: 520px; }
  .signature__mark { width: 150px; height: 38px; background: linear-gradient(90deg, #2b2b2b22, #2b2b2b0a); border-radius: 4px; }
  .signature__name { color: var(--purple); font-weight: 500; font-size: 12px; margin-top: 4px; }
  .signature__title { font-size: 9px; }

  .footer { position: absolute; left: 40px; font-size: 8px; line-height: 1.7; }
  .footer b { color: var(--purple); font-weight: 500; }
  .footer .sep { margin: 0 6px; }

  .body-copy { position: absolute; left: 40px; top: 130px; width: 460px; }
  .body-copy p { font-size: 8.5px; line-height: 1.6; margin-bottom: 16px; }

  .page-no { position: absolute; right: 40px; top: 612px; font-size: 8px; }
  .page-no b { color: var(--purple); font-weight: 500; }
</style>
</head>
<body>

<section class="sheet sheet--front">
  <div class="brand"><span class="brand__dot"></span><span class="brand__name">VERIDAN</span></div>
  <div class="bar" style="left:40px; top:110px; width:120px;"></div>
  <div class="rule" style="left:160px; top:112px; width:340px;"></div>

  <div class="recipient">
    <div class="recipient__label">To</div>
    <div class="recipient__name">Mara Ellison</div>
    <div>Manager</div>
    <div>Northfield Alloys Ltd.</div>
    <div class="recipient__date-label">Date:</div>
    <div>25-02-2020</div>
  </div>

  <div class="letter">
    <div class="letter__greeting">Dear Clients</div>
    <p>Lorem ipsum dolor sit amet, consectetuer adipiscing elit, sed diam nonummy nibh euismod tincidunt ut laoreet dolore magna aliquam erat volutpat. Ut wisi enim ad minim veniam, quis nostrud exerci tation ullamcorper suscipit lobortis nisl ut aliquip ex ea commodo consequat. Duis autem vel eum iriure dolor in hendrerit in vulputate velit esse molestie consequat, vel illum dolore eu feugiat nulla facilisis at vero eros et accumsan et iusto odio dignissim qui blandit praesent luptatum zzril delenit augue duis dolore te feugait nulla facilisi.</p>
    <p>Lorem ipsum dolor sit amet, cons ectetuer adipiscing elit, sed diam nonummy nibh euismod tincidunt ut laoreet dolore magna aliquam erat volutpat. Ut wisi enim ad minim veniam, quis nostrud exerci tation ullamcorper suscipit lobortis nisl ut aliquip ex ea commodo consequat.</p>
    <p>Lorem ipsum dolor sit amet, consectetuer adipiscing elit, sed diam nonummy nibh euismod tincidunt ut laoreet dolore magna aliquam erat volutpat. Ut wisi enim ad minim veniam, quis nostrud exerci tation ullamcorper suscipit lobortis nisl ut aliquip ex ea commodo consequat.</p>
    <p>Lorem ipsum dolor sit amet, cons ectetuer adipiscing elit, sed diam nonummy nibh euismod tincidunt ut laoreet dolore ma.</p>
  </div>

  <div class="signature">
    <div class="signature__mark" role="img" aria-label="Handwritten signature of Owen Carter"></div>
    <div class="signature__name">Owen Carter</div>
    <div class="signature__title">Vice President</div>
  </div>

  <div class="bar" style="left:40px; top:622px; width:150px;"></div>
  <div class="rule" style="left:190px; top:623px; width:310px;"></div>
  <div class="footer" style="top:636px;">
    <div><b>Tel:</b> 0100-555-0142<span class="sep">|</span><b>Fax:</b> 0100-555-0143<span class="sep">|</span><b>Email:</b> info@veridangroup.com</div>
    <div><b>Address:</b> 1420 Alder Lane, Suite #204, Westbrook, FL 32000</div>
  </div>
</section>

<section class="sheet sheet--inner">
  <div class="brand"><span class="brand__dot"></span><span class="brand__name">VERIDAN</span></div>
  <div class="rule" style="left:200px; top:74px; width:300px;"></div>

  <div class="body-copy">
    <p>Lorem ipsum dolor sit amet, consectetuer adipiscing elit, sed diam nonummy nibh euismod tincidunt ut laoreet dolore magna aliquam erat volutpat. Ut wisi enim ad minim veniam, quis nostrud exerci tation ullamcorper suscipit lobortis nisl ut aliquip ex ea commodo consequat. Duis autem vel eum iriure dolor in hendrerit in vulputate velit esse molestie consequat, vel illum dolore eu feugiat nulla facilisis at vero eros et accumsan et iusto odio dignissim qui blandit praesent luptatum zzril delenit augue duis dolore te feugait nulla facilisi.</p>
    <p>Lorem ipsum dolor sit amet, cons ectetuer adipiscing elit, sed diam nonummy nibh euismod tincidunt ut laoreet dolore magna aliquam erat volutpat. Ut wisi enim ad minim veniam, quis nostrud exerci tation ullamcorper suscipit lobortis nisl ut aliquip ex ea commodo consequat.</p>
    <p>Lorem ipsum dolor sit amet, consectetuer adipiscing elit, sed diam nonummy nibh euismod tincidunt ut laoreet dolore magna aliquam erat volutpat. Ut wisi enim ad minim veniam, quis nostrud exerci tation ullamcorper suscipit lobortis nisl ut aliquip ex ea commodo consequat. Duis autem vel eum iriure dolor in hendrerit in vulputate velit esse molestie consequat, vel illum dolore eu feugiat nulla facilisis at vero eros et accumsan et iusto odio dignissim qui blandit praesent luptatum zzril delenit augue duis dolore te feugait nulla facilisi.</p>
    <p>Lorem ipsum dolor sit amet, consectetuer adipiscing elit, sed diam nonummy nibh euismod tincidunt ut laoreet dolore magna aliquam erat volutpat. Ut wisi enim ad minim veniam, quis nostrud exerci tation ullamcorper suscipit lobortis nisl ut aliquip ex ea commodo consequat. Duis autem vel eum iriure dolor in hendrerit in vulputate velit esse molestie consequat, vel illum dolore eu feugiat nulla facilisis at vero eros et accumsan et iusto odio dignissim qui blandit praesent luptatum zzril delenit augue duis dolore te feugait nulla facilisi.</p>
    <p>Lorem ipsum dolor sit amet, cons ectetuer adipiscing elit, sed diam nonummy nibh euismod tincidunt ut laoreet dolore magna aliquam erat volutpat. Ut wisi enim ad minim veniam, quis nostrud exerci tation ullamcorper suscipit lobortis nisl ut aliquip ex ea commodo consequat.</p>
    <p>Lorem ipsum dolor sit amet, consectetuer adipiscing elit, sed diam nonummy nibh euismod tincidunt ut laoreet dolore magna aliquam erat volutpat. Ut wisi enim ad minim veniam, quis nostrud exerci tation ullamcorper suscipit lobortis nisl ut aliquip ex ea commodo consequat. Duis autem vel eum iriure dolor in hendrerit in vulputate velit esse molestie consequat, vel illum dolore eu feugiat nulla facilisis at vero eros et accumsan.</p>
  </div>

  <div class="page-no"><b>Pg No:</b> 01</div>
  <div class="rule" style="left:40px; top:630px; width:460px;"></div>
  <div class="footer" style="top:642px;">
    <div><b>Tel:</b> 0100-555-0142<span class="sep">|</span><b>Fax:</b> 0100-555-0143<span class="sep">|</span><b>Email:</b> info@veridangroup.com</div>
    <div><b>Address:</b> 1420 Alder Lane, Suite #204, Westbrook, FL 32000</div>
  </div>
</section>

</body>
</html>
```